Birch And Harbor Website A Website design for book editing

A website design for book editing

Our proofreading, editing and manuscript review packages are specifically tailored to help you publish the best possible version of your story.

NEED HELP PUBLISHING A BESTSELLER?

If you’re looking for professional book editing services from senior publishing industry insiders, look no further. Besides editing, we can also answer all your publishing questions and get you started building your author platform.

OUR SERVICES

We've carefully structured our packages to maximize value for every budget.

PRICING

$.02
PER WORD
Proofreading
Line Edit (Copy-editing)
Fix spelling and grammar
Sales copy/summary revision

$.04
PER WORD
Proofreading
Line Edit (Copy-editing)
Fix spelling and grammar
Organization and content
Plot and pacing
Manuscript Review

$.06
PER WORD
Proofreading
Line Edit (Copy-editing)
Fix spelling and grammar
Organization and content
Plot and pacing
Manuscript Review
Formatting (print and ebook)
Pre-publication proofread

OUR PROCESS

Send us a sample of your book. Our caffeine-fueled, eagle-eyed editors will go through it and then email you with their comments and suggestions. You can ask them any questions you want. They will look for…

Typos and grammatical errors.
Spelling and word choice issues
Punctuation and style
Word choice, clarity and flow.
Sentence structure and craft
If your writing is already clean, then they’ll discuss bigger picture things with you, like theme, concept, purpose, audience, potential market and branding (including title, subtitle, and tagline or elevator pitch).

Once you feel comfortable and confident in an editor’s expertise, skill and knowledge, and are ready to move ahead, we’ll send an invoice for the first half of the total word count so the editor can get started. We’ll charge the rest when the project is close to completion.

Target Market(s)

Authors

Industry/Entity Type

Book Publisher

Coding

Coded - Design and coding required

Number of Pages Required

1 page

Requirements
Must have
• OUR SERVICES
• We've carefully structured our packages to maximize value for every budget.
• PRICING
• $.02
• PER WORD
• Proofreading
• Line Edit (Copy-editing)
• Fix spelling and grammar
• Sales copy/summary revision
• $.04
• PER WORD
• Proofreading
• Organization and content
• Plot and pacing
• Manuscript Review
• $.06
• PER WORD
• Proofreading
• Plot and pacing
• Manuscript Review
• Formatting (print and ebook)
• Pre-publication proofread

```html
<!DOCTYPE html>
<html lang="en">
<head>
<meta charset="utf-8">
<title>Birch And Harbor – Book Editing</title>
<link href="https://fonts.googleapis.com/css2?family=Poppins:wght@400;500;600&family=Open+Sans:wght@400;600&display=swap" rel="stylesheet">
<style>
:root{
  --red:#e3101e;
  --red-deep:#b0050f;
  --ink:#1c1c1c;
  --text:#444;
  --muted:#777;
  --dark:#232323;
  --black:#111;
  --white:#fff;
  --hero-bg:#eef0f4;
}
*{box-sizing:border-box;margin:0;padding:0}
html,body{width:1200px;height:4423px;overflow:hidden}
body{position:relative;background:var(--white);font-family:"Open Sans",Arial,sans-serif;color:var(--text)}
.abs{position:absolute}
.heading{font-family:"Poppins",Arial,sans-serif;font-weight:400;color:var(--ink);letter-spacing:1px}
.section-title{position:absolute;left:0;width:1200px;text-align:center;font-size:36px}

/* header */
.brand{left:88px;top:62px;display:flex;align-items:center;gap:12px;font-family:"Poppins",Arial,sans-serif;font-weight:600;font-size:34px;color:var(--red)}
.brand-dot{width:22px;height:22px;border-radius:50%;background:var(--red)}
.phone{left:758px;top:43px;font-size:17px;color:var(--ink);display:flex;align-items:center;gap:8px;white-space:nowrap}
.search{left:930px;top:34px;width:182px;height:38px;border:1.5px solid #555;border-radius:19px;font-size:14px;padding:9px 16px;color:#333}
.search svg{position:absolute;right:12px;top:10px}
.nav{left:472px;top:96px;display:flex;gap:0;font-size:17px;color:#333}
.nav a{text-decoration:none;color:inherit;width:106px}
.nav a.active{color:var(--red)}

/* hero */
.hero{left:0;top:153px;width:1200px;height:630px;background:linear-gradient(90deg,#f5f6f8 0%,#e9ebef 100%);overflow:hidden}
.hero-photo{position:absolute;left:470px;top:0;width:730px;height:630px;background:linear-gradient(120deg,#e7e9ee 0%,#cfd6e2 45%,#8fa6c6 70%,#c8ced8 100%)}
.hero-title{left:88px;top:385px;font-size:48px;line-height:70px}
.hero-title em{font-style:normal;color:var(--red)}
.dots{left:88px;top:545px;display:flex;gap:6px}
.dots span{width:22px;height:22px;border-radius:50%;background:#555;display:flex;align-items:center;justify-content:center}

/* about */
.about-frame{left:120px;top:890px;width:412px;height:318px;border:3px solid var(--red)}
.about-photo{left:153px;top:914px;width:394px;height:316px;background:linear-gradient(135deg,#b9c2cc,#6e7d8f 60%,#d9dde2)}
.play{left:319px;top:1041px;width:62px;height:62px;border-radius:50%;background:rgba(30,30,30,.75)}
.about-title{left:590px;top:928px;font-size:36px}
.about-text{left:590px;top:986px;width:500px;font-size:13px;line-height:27px;color:#555}
.btn-red{background:var(--red);color:var(--white);font-size:13px;border-radius:3px;text-align:center}
.about-btn{left:592px;top:1173px;width:96px;height:32px;line-height:32px}

/* pricing */
.pricing{left:0;top:1335px;width:1200px;height:685px;background:linear-gradient(180deg,#2a2a2a,#1d1d1d)}
.pricing .section-title{color:var(--white);top:82px}
.card{position:absolute;background:var(--white);text-align:center;color:#222;border-radius:3px}
.card .price{font-family:"Poppins",Arial,sans-serif;font-size:56px;line-height:56px;margin-top:30px}
.card .per{font-family:"Poppins",Arial,sans-serif;font-weight:600;font-size:22px;line-height:26px;margin-top:16px}
.card .kind{font-size:18px;line-height:24px}
.card ul{list-style:none;font-size:13px;line-height:25px;margin-top:20px}
.card .more{position:absolute;left:50%;transform:translateX(-50%);width:170px;height:38px;line-height:34px;border:2px solid #ddd;border-radius:19px;font-size:13px;box-shadow:0 2px 6px rgba(0,0,0,.12)}
.card.featured{background:var(--red);color:var(--white)}
.card.featured .price{margin-top:30px}
.card.featured .per{margin-top:10px}
.card.featured ul{margin-top:16px}
.card.featured .more{background:var(--white);color:#222;border-color:var(--white)}

/* services */
.services .section-title{top:2175px}
.svc-ring{left:436px;top:2255px;width:324px;height:324px;border-radius:50%;border:2px solid #333}
.svc-art{left:520px;top:2330px;width:156px;height:176px;border-radius:50%;background:radial-gradient(#f4c9cc,#fff 70%)}
.svc-icon{width:54px;height:54px;border-radius:50%;background:var(--red);display:flex;align-items:center;justify-content:center}
.svc{font-size:14px;line-height:20px;color:#333;width:300px}
.svc h3{font-family:"Poppins",Arial,sans-serif;font-weight:400;font-size:20px;color:#222;margin-bottom:6px}
.svc.left{text-align:right}

/* contact */
.contact{left:0;top:2742px;width:1200px;height:690px;background:linear-gradient(180deg,#b20814,#a1060f)}
.contact .section-title{color:var(--white);top:102px}
.field{position:absolute;left:162px;width:430px;height:50px;background:var(--white);border-radius:2px;font-size:15px;color:#333;padding:14px 14px}
.submit{left:162px;width:106px;height:30px;background:var(--black);color:var(--white);font-size:14px;text-align:center;line-height:30px}
.info{left:668px;color:var(--white);font-size:16px;line-height:26px}
.info h4{font-family:"Poppins",Arial,sans-serif;font-weight:600;font-size:16px;letter-spacing:1px;margin-bottom:6px}
.info p{display:flex;gap:12px;align-items:flex-start}

/* process */
.process .section-title{top:3508px}
.process-intro{left:230px;top:3572px;width:740px;text-align:center;font-size:16px;line-height:32px;color:#444}
.step{position:absolute;top:3720px;width:295px;height:272px;border:3px solid var(--red);border-radius:22px;background:var(--white);box-shadow:0 6px 14px rgba(0,0,0,.12);text-align:center;padding:48px 30px 0}
.step h3{font-family:"Poppins",Arial,sans-serif;font-weight:400;font-size:20px;line-height:28px;color:#222}
.step p{font-size:13px;line-height:22px;margin-top:26px;color:#444}
.step-art{position:absolute;left:14px;top:14px;right:14px;bottom:14px;border-radius:12px;background:linear-gradient(135deg,#fbe3c9,#f6b24b 40%,#3d5fb5 75%,#e8eef8)}
.arrow{width:46px;height:46px;border-radius:50%;border:1.5px solid #aaa;background:var(--white);display:flex;align-items:center;justify-content:center}

/* footer */
.footer{left:0;top:4112px;width:1200px;height:311px;background:var(--black)}
.social{left:970px;top:4158px;display:flex;gap:12px}
.social span{width:28px;height:28px;background:#9c9c9c;border-radius:3px}
.foot-brand{left:94px;top:4256px;display:flex;align-items:center;gap:10px;font-family:"Poppins",Arial,sans-serif;font-weight:600;font-size:30px;color:var(--white)}
.foot-brand .brand-dot{width:18px;height:18px;background:var(--white)}
.newsletter{left:616px;top:4250px;font-family:"Poppins",Arial,sans-serif;font-size:16px;letter-spacing:.5px;color:var(--white)}
.email-box{left:831px;top:4232px;width:284px;height:54px;border:1.5px solid #ccc;border-radius:27px;color:#bbb;font-size:14px;padding:16px 24px}
.email-box span{position:absolute;right:14px;top:14px;width:22px;height:22px;border-radius:50%;background:#ccc}
.foot-nav{left:92px;top:4354px;display:flex;gap:38px;font-size:13px;color:var(--white)}
.copyright{left:870px;top:4354px;font-size:13px;color:var(--white)}
</style>
</head>
<body>

<!-- header -->
<div class="abs brand"><span class="brand-dot"></span>Birch And Harbor</div>
<div class="abs phone">
  <svg width="15" height="15" viewBox="0 0 24 24"><path fill="#e3101e" d="M6.6 10.8a15 15 0 0 0 6.6 6.6l2.2-2.2a1 1 0 0 1 1-.25 11.4 11.4 0 0 0 3.6.57 1 1 0 0 1 1 1V20a1 1 0 0 1-1 1A17 17 0 0 1 3 4a1 1 0 0 1 1-1h3.5a1 1 0 0 1 1 1c0 1.25.2 2.45.57 3.57a1 1 0 0 1-.25 1z"/></svg>
  1-800-555-0142
</div>
<div class="abs search">Search
  <svg width="16" height="16" viewBox="0 0 24 24"><circle cx="10" cy="10" r="6.5" fill="none" stroke="#333" stroke-width="2.5"/><path d="M15 15l6 6" stroke="#333" stroke-width="2.5"/></svg>
</div>
<nav class="abs nav">
  <a class="active">Home</a><a>About</a><a>Services</a><a>Pricing</a><a>Process</a><a>Contact</a>
</nav>

<!-- hero -->
<section class="abs hero">
  <div class="hero-photo" role="img" aria-label="Photo of a young woman with glasses reading a book in a library"></div>
  <svg class="abs" style="left:0;top:0" width="1200" height="630" viewBox="0 0 1200 630">
    <polygon points="500,630 1200,510 1200,630" fill="#fff"/>
    <polygon points="700,630 1200,540 1200,630" fill="#e3101e"/>
    <polygon points="500,630 1200,585 1200,630" fill="#fff"/>
  </svg>
</section>
<h1 class="abs heading hero-title">NEED HELP <em>PUBLISHING</em><br>A BESTSELLER?</h1>
<div class="abs dots">
  <span><svg width="8" height="10" viewBox="0 0 8 10"><path d="M6 1 2 5l4 4" stroke="#fff" stroke-width="1.6" fill="none"/></svg></span>
  <span><svg width="8" height="10" viewBox="0 0 8 10"><path d="M2 1l4 4-4 4" stroke="#fff" stroke-width="1.6" fill="none"/></svg></span>
</div>

<!-- about -->
<div class="abs about-frame"></div>
<div class="abs about-photo" role="img" aria-label="Photo of two colleagues reviewing a manuscript at a desk"></div>
<div class="abs play"><svg width="62" height="62" viewBox="0 0 62 62"><polygon points="25,19 44,31 25,43" fill="#fff"/></svg></div>
<h2 class="abs heading about-title">About us</h2>
<p class="abs about-text">It is a long established fact that a reader will be distracted by the readable content of a page when looking at its layout. The point of using Lorem Ipsum is that it has a more-or-less normal distribution of letters, as opposed to using 'Content here, content here', making it look like readable English. Many desktop publishing packages and web page editors now use Lorem Ipsum as their default model text, and a search for 'lorem ipsum'</p>
<div class="abs btn-red about-btn">Read More</div>

<!-- pricing -->
<section class="abs pricing">
  <h2 class="heading section-title">PRICING</h2>
  <div class="card" style="left:200px;top:192px;width:272px;height:345px">
    <div class="price">$.02</div><div class="per">PER WORD</div><div class="kind">Proofreading</div>
    <ul><li>Line Edit (Copy-editing)</li><li>Fix spelling and grammar</li><li>Sales copy/summary revision</li></ul>
    <div class="more" style="top:272px">View More</div>
  </div>
  <div class="card featured" style="left:476px;top:168px;width:278px;height:400px">
    <div class="price">$.04</div><div class="per">PER WORD</div><div class="kind">Proofreading</div>
    <ul><li>Line Edit (Copy-editing)</li><li>Fix spelling and grammar</li><li>Sales copy/summary revision</li><li>Organization and content</li><li>Plot and pacing</li><li>Manuscript Review</li></ul>
    <div class="more" style="top:336px">Sign Up</div>
  </div>
  <div class="card" style="left:758px;top:192px;width:266px;height:345px">
    <div class="price">$.06</div><div class="per">PER WORD</div><div class="kind">Proofreading</div>
    <ul><li>Line Edit (Copy-editing)</li><li>Fix spelling and grammar</li><li>Sales copy/summary revision</li></ul>
    <div class="more" style="top:272px">View More</div>
  </div>
</section>
<svg class="abs" style="left:0;top:2015px" width="1200" height="64" viewBox="0 0 1200 64">
  <polygon points="0,0 470,0 0,64" fill="#e3101e"/>
  <polygon points="0,0 1200,0 1200,5 0,5" fill="#1d1d1d"/>
</svg>

<!-- services -->
<section class="services">
  <h2 class="heading section-title">OUR SERVICES</h2>
  <div class="abs svc-ring"></div>
  <div class="abs svc-art" role="img" aria-label="Red footprint illustration"></div>
  <div class="abs svc-icon" style="left:451px;top:2302px"><svg width="22" height="22" viewBox="0 0 24 24"><path d="M4 20l1-4L16 5l3 3L8 19z" fill="#fff"/></svg></div>
  <div class="abs svc-icon" style="left:684px;top:2308px"><svg width="22" height="22" viewBox="0 0 24 24"><rect x="5" y="3" width="14" height="18" rx="2" fill="#fff"/><path d="M8 8h8M8 12h8" stroke="#e3101e" stroke-width="2"/></svg></div>
  <div class="abs svc-icon" style="left:451px;top:2502px"><svg width="22" height="22" viewBox="0 0 24 24"><path d="M6 2h8l5 5v15H6z" fill="#fff"/><path d="M9 12h7M9 16h7" stroke="#e3101e" stroke-width="2"/></svg></div>
  <div class="abs svc-icon" style="left:689px;top:2502px"><svg width="22" height="22" viewBox="0 0 24 24"><rect x="3" y="4" width="18" height="12" rx="1" fill="#fff"/><path d="M9 20h6M12 16v4" stroke="#fff" stroke-width="2"/></svg></div>
  <div class="abs svc left" style="left:113px;top:2300px"><h3>Porro quisquam</h3>The point of using Lorem Ipsum is that it has a more-or-less normal distribu</div>
  <div class="abs svc" style="left:778px;top:2300px"><h3>Ipsum quia dolor</h3>The point of using Lorem Ipsum is that it has a more-or-less normal distribution</div>
  <div class="abs svc left" style="left:113px;top:2492px"><h3>Dolorem ipsum</h3>The point of using Lorem Ipsum is that it has a more-or-less normal distribu</div>
  <div class="abs svc" style="left:778px;top:2492px"><h3>Neque porro ipsum</h3>The point of using Lorem Ipsum is that it has a more-or-less normal distribution</div>
</section>

<!-- contact -->
<section class="abs contact">
  <h2 class="heading section-title">CONTACT</h2>
</section>
<div class="field" style="top:2962px">Name</div>
<div class="field" style="top:3022px">Email id</div>
<div class="field" style="top:3084px">Phone</div>
<div class="field" style="top:3146px">Messages</div>
<div class="abs submit" style="top:3212px">Submit</div>
<div class="abs info" style="top:2950px">
  <h4>LOCATION</h4>
  <p><svg width="14" height="18" viewBox="0 0 14 18" style="margin-top:4px"><path d="M7 0a7 7 0 0 1 7 7c0 5-7 11-7 11S0 12 0 7a7 7 0 0 1 7-7z" fill="#fff"/><circle cx="7" cy="7" r="2.5" fill="#b20814"/></svg><span>Larkspur Court 210 Alder Street Suite 18<br>Fairview, Oregon 97024</span></p>
  <h4 style="margin-top:22px">CONTACT US</h4>
  <p><svg width="16" height="12" viewBox="0 0 16 12" style="margin-top:7px"><rect width="16" height="12" fill="#fff"/><path d="M0 0l8 6 8-6" stroke="#b20814" fill="none"/></svg>hello@birchharbor.test</p>
  <p style="margin-top:8px"><svg width="16" height="16" viewBox="0 0 24 24" style="margin-top:5px"><path fill="#fff" d="M6.6 10.8a15 15 0 0 0 6.6 6.6l2.2-2.2a1 1 0 0 1 1-.25 11.4 11.4 0 0 0 3.6.57 1 1 0 0 1 1 1V20a1 1 0 0 1-1 1A17 17 0 0 1 3 4a1 1 0 0 1 1-1h3.5a1 1 0 0 1 1 1c0 1.25.2 2.45.57 3.57a1 1 0 0 1-.25 1z"/></svg>503.555.0187</p>
  <p style="margin-top:8px"><svg width="16" height="16" viewBox="0 0 16 16" style="margin-top:5px"><rect x="1" y="5" width="14" height="10" fill="#fff"/><rect x="4" y="1" width="8" height="5" fill="#fff"/></svg>503.555.0193</p>
</div>
<svg class="abs" style="left:0;top:3360px" width="1200" height="72" viewBox="0 0 1200 72">
  <polygon points="0,72 1200,0 1200,72" fill="#fff"/>
  <polygon points="640,72 1200,30 1200,72" fill="#111"/>
  <polygon points="0,72 1200,58 1200,72" fill="#fff"/>
</svg>

<!-- process -->
<section class="process">
  <h2 class="heading section-title">OUR PROCESS</h2>
  <p class="abs process-intro">Send us a sample of your book. Our caffeine-fueled, eagle-eyed editors will go through it and then email you with their comments and suggestions. You can ask them any questions you want. They will look for…</p>
  <div class="step" style="left:133px"><h3>Typos and<br>grammatical errors.</h3><p>The point of using Lorem Ipsum is that it has a more-or-less normal distribution of letters, as opposed to using 'Content here,</p></div>
  <div class="step" style="left:452px"><div class="step-art" role="img" aria-label="Illustration of books, a calendar and a clock for the editing workflow"></div></div>
  <div class="step" style="left:772px"><h3>Word choice<br>clarity and flow.</h3><p>The point of using Lorem Ipsum is that it has a more-or-less normal distribution of letters, as opposed to using 'Content here,</p></div>
  <div class="abs arrow" style="left:56px;top:3834px"><svg width="10" height="16" viewBox="0 0 10 16"><path d="M8 1 2 8l6 7" stroke="#555" stroke-width="1.6" fill="none"/></svg></div>
  <div class="abs arrow" style="left:1097px;top:3834px"><svg width="10" height="16" viewBox="0 0 10 16"><path d="M2 1l6 7-6 7" stroke="#555" stroke-width="1.6" fill="none"/></svg></div>
</section>

<!-- footer -->
<footer class="abs footer"></footer>
<svg class="abs" style="left:0;top:4100px" width="1200" height="90" viewBox="0 0 1200 90">
  <polygon points="0,12 1200,12 1200,0 0,0" fill="#fff"/>
  <polygon points="0,12 1200,12 0,90" fill="#e3101e"/>
  <polygon points="0,12 1200,12 0,70" fill="#fff"/>
  <polygon points="0,70 1200,12 1200,90 0,90" fill="#111"/>
</svg>
<div class="abs social"><span></span><span></span><span></span><span></span></div>
<div class="abs foot-brand"><span class="brand-dot"></span>Birch And Harbor</div>
<div class="abs newsletter">JOIN OUR NEWSLETTER</div>
<div class="abs email-box">Email address<span></span></div>
<div class="abs foot-nav"><span>Home</span><span>About</span><span>Services</span><span>Pricing</span><span>Process</span><span>Contact</span></div>
<div class="abs copyright">Copyright © 2018. All Rights Reserved</div>

</body>
</html>
```